Realty Group Needs Classy, Contemporary Letterhead Design

We need a letterhead design for a new realty company located in NY, USA. We buy investment properties to rehabilitate and or keep in our rental portfolio.

```html
<!DOCTYPE html>
<html lang="en">
<head>
<meta charset="utf-8">
<title>Meridian Realty Group Letterhead</title>
<link href="https://fonts.googleapis.com/css2?family=Arimo:ital,wght@0,400;0,700;1,400&family=Poppins:wght@400;500&display=swap" rel="stylesheet">
<style>
  :root {
    --purple: #4f2a87;
    --purple-soft: #e9e5f1;
    --header-grey: #ecebf0;
    --ink: #1c1c1c;
    --backdrop: #c4c4c6;
    --paper: #ffffff;
  }
  * { box-sizing: border-box; margin: 0; padding: 0; }
  html, body { width: 1200px; height: 1089px; overflow: hidden; }
  body {
    background: var(--backdrop);
    font-family: "Arimo", Arial, sans-serif;
    color: var(--ink);
    position: relative;
  }
  .letterhead {
    position: absolute;
    left: 255px; top: 30px;
    width: 730px; height: 1030px;
    background: var(--paper);
    box-shadow: 0 10px 30px rgba(0,0,0,0.18);
    overflow: hidden;
  }
  .header-band { position: absolute; left: 0; top: 0; width: 100%; height: 230px; }
  .brand {
    position: absolute; right: 60px; top: 70px;
    display: flex; align-items: center; gap: 10px;
    font-family: "Arimo", Arial, sans-serif;
    font-weight: 700; font-size: 30px; color: var(--purple);
    letter-spacing: 0.5px;
  }
  .brand-dot { width: 14px; height: 14px; border-radius: 50%; background: var(--purple); }
  .letter { position: absolute; left: 70px; top: 150px; width: 590px; font-size: 15px; line-height: 1.45; }
  .letter-date { margin-bottom: 26px; }
  .recipient-name { font-weight: 700; font-size: 16px; }
  .recipient { margin-bottom: 24px; }
  .letter p { margin-bottom: 16px; text-align: justify; }
  .signature { width: 120px; height: 34px; margin: 10px 0 6px; background: linear-gradient(90deg, #e6e6e6, #f3f3f3); border-radius: 4px; }
  .sender-name { font-weight: 700; font-size: 18px; }
  .archer-mark { position: absolute; left: 80px; bottom: 70px; width: 240px; height: 140px; }
  .footer-band {
    position: absolute; left: 0; bottom: 0; width: 360px; height: 56px;
    background: var(--purple);
    border-top-right-radius: 14px;
    display: flex; align-items: center; gap: 40px; padding-left: 36px;
    font-family: "Poppins", sans-serif; font-size: 12px; color: #fff;
  }
  .footer-item { display: flex; align-items: center; gap: 6px; }
  .footer-address {
    position: absolute; left: 378px; bottom: 14px;
    font-family: "Poppins", sans-serif; font-weight: 500; font-size: 12px; color: var(--purple);
  }
</style>
</head>
<body>
  <main class="letterhead">
    <svg class="header-band" viewBox="0 0 730 230" preserveAspectRatio="none" aria-hidden="true">
      <defs>
        <linearGradient id="headerFade" x1="0" y1="0" x2="1" y2="0">
          <stop offset="0" stop-color="#f4f3f7"/>
          <stop offset="1" stop-color="#e2e1e8"/>
        </linearGradient>
      </defs>
      <path d="M0 0 H730 V230 C520 200 260 110 0 60 Z" fill="url(#headerFade)"/>
    </svg>

    <div class="brand"><span class="brand-dot"></span>MERIDIAN <span style="font-weight:700">Realty Group, LLC</span></div>

    <section class="letter">
      <div class="letter-date">4th September 20XX</div>
      <div class="recipient">
        <div class="recipient-name">Ronny Reader</div>
        <div>CEO, Company Name</div>
        <div>123 Address St.</div>
        <div>Anytown, ST 12345</div>
      </div>
      <p style="margin-bottom:4px;text-align:left">Dear Mr. Reader,</p>
      <p>Lorem ipsum dolor sit amet, consectetuer adipiscing elit, sed diam nonummy nibh euismod tincidunt ut laoreet dolore magna aliquam erat volutpat. Ut wisi enim ad minim veniam, quis nostrud exerci tation ullamcorper suscipit lobortis nisl ut aliquip ex ea commodo consequat.</p>
      <p>Duis autem vel eum iriure dolor in hendrerit in vulputate velit esse molestie consequat, vel illum dolore eu feugiat nulla facilisis at vero eros et accumsan.</p>
      <p>Nam liber tempor cum soluta nobis eleifend option congue nihil imperdiet doming id quod mazim placerat facer possim assum. Typi non habent claritatem insitam; est usus legentis in iis qui facit eorum claritatem. Investigationes demonstraverunt lectores legere me lius quod ii legunt saepius.</p>
      <p style="margin-bottom:0;text-align:left">Sincerely,</p>
      <div class="signature" role="img" aria-label="Handwritten signature"></div>
      <div class="sender-name">Your Name</div>
    </section>

    <svg class="archer-mark" viewBox="0 0 240 140" role="img" aria-label="Faint decorative archer figure">
      <ellipse cx="120" cy="80" rx="115" ry="58" fill="var(--purple-soft)"/>
    </svg>

    <footer class="footer-band">
      <span class="footer-item">
        <svg width="11" height="11" viewBox="0 0 24 24" aria-hidden="true"><path fill="#fff" d="M6.6 10.8a15.1 15.1 0 0 0 6.6 6.6l2.2-2.2c.3-.3.7-.4 1-.2 1.1.4 2.3.6 3.6.6.6 0 1 .4 1 1V20c0 .6-.4 1-1 1A17 17 0 0 1 3 4c0-.6.4-1 1-1h3.5c.6 0 1 .4 1 1 0 1.3.2 2.5.6 3.6.1.3 0 .7-.2 1z"/></svg>
        (555) 014-2290
      </span>
      <span class="footer-item">
        <svg width="11" height="11" viewBox="0 0 24 24" aria-hidden="true"><circle cx="12" cy="12" r="10" fill="#fff"/><path d="M2 12h20M12 2c3 3 3 17 0 20M12 2c-3 3-3 17 0 20" stroke="var(--purple)" stroke-width="1.6" fill="none"/></svg>
        www.meridianrealtyllc.com
      </span>
    </footer>
    <div class="footer-address">42 Linden Avenue, Suite 200, Maple Ridge, New York 10520</div>
  </main>
</body>
</html>
```